A private security company called "Tavron Security Services Ltd"

Hello everybody,

We need a web page for a company based in NZ. It is mainly an informative website so it would be wonderful if the designer puts their absolute best into making it a website that I would really appreciate. The website needs to show professionalism and also needs to make our web surfers find the information they need in a click. the company's colour is black and silver, and if those two colours could be integrated into the website it would be absolutely lovely. Please do contact me for any information.

Sincerely,
Dorian Vaskel

Industry/Entity Type

Security

```html
<!DOCTYPE html>
<html lang="en">
<head>
<meta charset="utf-8">
<title>Tavron Security Services Ltd</title>
<link rel="stylesheet" href="https://fonts.googleapis.com/css2?family=Open+Sans:wght@300;400;600;700&display=swap">
<style>
:root{
  --ink:#111;
  --black:#000;
  --silver:#d9d9d9;
  --white:#fff;
  --muted:#8a8a8a;
  --panel:#f4f4f4;
  --panel-line:#e3e3e3;
  --sky:#3d8fd6;
  --sky-light:#bcdcf4;
}
*{margin:0;padding:0;box-sizing:border-box}
html,body{width:1016px;height:1200px;overflow:hidden;background:var(--black)}
body{font-family:"Open Sans",sans-serif;color:var(--ink)}
.page{position:relative;width:1016px;height:1200px;overflow:hidden;
  background:radial-gradient(ellipse 260px 340px at 40px 640px,#2a2a2a 0%,transparent 70%),
             radial-gradient(ellipse 200px 300px at 990px 870px,#2a2a2a 0%,transparent 70%),
             var(--black)}
.header-scene{position:absolute;left:300px;top:0;width:420px;height:146px;
  background:radial-gradient(ellipse at 60% 40%,#4a4a4a 0%,#1c1c1c 50%,transparent 75%)}
.brand{position:absolute;left:93px;top:82px;display:flex;align-items:center;gap:8px;color:var(--white);
  font-weight:600;font-size:13px;letter-spacing:.5px;white-space:nowrap}
.brand-mark{width:14px;height:14px;background:var(--silver)}
.phone{position:absolute;right:93px;top:44px;color:var(--white);font-size:20px;font-weight:300;white-space:nowrap}
.phone b{font-weight:600}
.search{position:absolute;left:713px;top:80px;width:210px;height:29px;background:var(--white);
  border:2px solid var(--white);border-radius:3px;display:flex}
.search span{flex:1;font-size:12px;padding:5px 6px;color:#333}
.search button{width:42px;background:linear-gradient(#333,#000);color:var(--white);border:0;border-radius:2px;
  font-family:inherit;font-size:12px}
.nav{position:absolute;left:93px;top:146px;width:830px;height:39px;
  background:linear-gradient(#4a4a4a,#111 60%,#000)}
.nav a{position:absolute;top:12px;color:var(--white);font-size:12px;text-decoration:none;white-space:nowrap}
.nav .active{left:14px;top:6px;padding:4px 10px;background:linear-gradient(#fff,#d4d4d4);
  color:#111;font-weight:700;border-radius:2px}
.hero{position:absolute;left:93px;top:185px;width:830px;height:350px;
  background:linear-gradient(180deg,var(--sky) 0%,var(--sky-light) 45%,#cfd6da 60%,#6d7d77 100%)}
.hero-curve{position:absolute;left:0;bottom:0}
.hero-caption{position:absolute;left:0;top:92px;width:462px;height:137px;background:rgba(10,15,25,.78);
  color:var(--white);padding:20px 20px 0}
.hero-caption h1{font-size:21px;line-height:28px;font-weight:700;margin-bottom:10px;white-space:nowrap}
.hero-caption h1 span{font-weight:300;margin-left:8px}
.hero-caption p{font-size:10.5px;line-height:15.5px}
.content{position:absolute;left:93px;top:535px;width:830px;height:625px;background:var(--white)}
.services{position:absolute;left:17px;top:31px;width:216px;height:329px;background:var(--panel);
  border:1px solid var(--panel-line);border-radius:3px;padding:10px 14px}
.services h2,.testimonials h2{font-size:25px;font-weight:300}
.services ul{list-style:none;margin-top:8px}
.services li{font-size:11px;color:var(--muted);font-weight:300;height:34px;padding-left:12px;position:relative;white-space:nowrap}
.services li::before{content:"";position:absolute;left:2px;top:7px;width:3px;height:3px;background:#aaa;border-radius:50%}
.testimonials{position:absolute;left:23px;top:382px;width:210px}
.avatar{position:absolute;left:0;top:39px;width:58px;height:52px;background:linear-gradient(#5a6d80,#2d3844)}
.reviewer{position:absolute;left:70px;top:44px;font-size:12px;font-weight:600}
.date{position:absolute;left:70px;top:75px;font-size:10px;color:var(--muted)}
.quote{position:absolute;left:0;top:109px;font-size:10.5px;line-height:21px;color:var(--muted);font-weight:300;white-space:nowrap}
.quote b{font-size:34px;color:#bbb;font-weight:400;vertical-align:-14px;line-height:0;margin-right:4px}
.btn{display:inline-block;background:linear-gradient(#3a3a3a,#000);color:var(--white);border-radius:2px}
.testimonials .btn{position:absolute;left:0;top:178px;font-size:11px;padding:5px 9px}
.welcome{position:absolute;left:272px;top:32px;width:520px}
.welcome h2{font-size:25px;font-weight:300;letter-spacing:-.5px}
.welcome h2 b{font-weight:700}
.welcome p{font-size:11px;line-height:18.6px;color:var(--muted);font-weight:300}
.welcome .lead{margin-top:10px}
.welcome h3{font-size:13px;font-weight:600;margin-top:16px;line-height:18px}
.welcome u{color:#111}
.welcome .btn{font-size:12px;padding:7px 18px;margin-top:18px;margin-left:-2px}
.features{position:absolute;left:272px;top:368px;width:520px;height:220px}
.feature{position:absolute;top:0;width:169px}
.feature .thumb{height:108px}
.feature h4{font-size:14px;font-weight:400;margin-top:14px;white-space:nowrap}
.feature p{font-size:10.5px;line-height:18.6px;color:var(--muted);font-weight:300;margin-top:6px}
.footer{position:absolute;left:0;top:1172px;width:1016px;text-align:center;color:var(--white);font-size:11px}
</style>
</head>
<body>
<div class="page">
  <div class="header-scene" role="img" aria-label="Close-up of a dark security camera"></div>
  <div class="brand"><span class="brand-mark"></span>TAVRON SECURITY SERVICES LTD</div>
  <div class="phone"><b>Call:</b> 021 555 0148</div>
  <div class="search"><span>Search</span><button>GO</button></div>

  <nav class="nav">
    <a class="active" href="#">HOME</a>
    <a href="#" style="left:97px">About Us</a>
    <a href="#" style="left:178px">Security Services</a>
    <a href="#" style="left:296px">Why Us</a>
    <a href="#" style="left:368px">Testimonials</a>
    <a href="#" style="left:466px">Contact Us</a>
  </nav>

  <section class="hero" role="img" aria-label="Security camera mounted above a street of modern townhouses under a blue sky">
    <div class="hero-caption">
      <h1>Newzealand’s Best<span>Security Company</span></h1>
      <p>It is a long established fact that a reader will be distracted by the readable content of a page when looking at its layout. The point of using Lorem Ipsum is that it has a more-or-less normal distribution of letters</p>
    </div>
    <svg class="hero-curve" width="830" height="20" viewBox="0 0 830 20"><path d="M0 20 L0 14 Q415 -4 830 12 L830 20 Z" fill="#fff"/></svg>
  </section>

  <main class="content">
    <aside class="services">
      <h2>Services</h2>
      <ul>
        <li>Lorem ipsum dolor consectetur</li>
        <li>Adipisicing elit sed do eiusmod</li>
        <li>Tempor incididunt ut labore et</li>
        <li>Dolore magna aliqua</li>
        <li>Ut enim ad minim veniam</li>
        <li>Quis nostrud exercitation</li>
        <li>Laboris nisi ut aliquip commodo</li>
        <li>Duis irure dolor reprehenderit</li>
      </ul>
    </aside>

    <aside class="testimonials">
      <h2>Testimonials</h2>
      <div class="avatar" role="img" aria-label="Portrait of the client"></div>
      <div class="reviewer">Leon Hartwell</div>
      <div class="date">6/23/2014</div>
      <p class="quote"><b>“</b>Lorem ipsum dolor consectetur<br>Adipisicing elit sed do eiusmod Tempor<br>incididunt ut labore et Dolore magna.</p>
      <span class="btn">Read More</span>
    </aside>

    <section class="welcome">
      <h2>Welcome to <b>Tavron</b></h2>
      <p class="lead">Lorem ipsum dolor sit amet, consectetur adipisicing elit, sed do eiusmod tempor incididunt ut labore et dolore magna aliqua. Ut enim ad minim veniam, quis nostrud exercitation ullamco laboris nisi ut aliquip ex ea commodo consequat. Duis aute irure dolor in reprehenderit in voluptate velit esse cillum dolore eu fugiat nulla pariatur. Excepteur sint occaecat cupidatat non proident, sunt in culpa qui officia deserunt mollit anim id est laborum</p>
      <h3>Lorem ipsum dolor sit amet consectetur</h3>
      <p>sed do eiusmod tempor incididunt ut labore et dolore magna aliqua. Ut enim ad minim veniam, quis nostrud exercitation ullamco laboris nisi ut aliquip ex ea commodo consequat. Duis aute irure dolor in reprehenderit in voluptate velit esse <u>cillum dolore eu fugiat nulla pariatur</u>. Excepteur sint occaecat cupidatat non proident, sunt in culpa qui officia deserunt mollit anim id est laborum</p>
      <span class="btn">Read More</span>
    </section>

    <section class="features">
      <div class="feature" style="left:0">
        <div class="thumb" role="img" aria-label="White security camera on a blue wall" style="background:linear-gradient(90deg,#2d6fc0,#6aa3e0)"></div>
        <h4>Camra System</h4>
        <p>Adipisicing elit eiusmod Tempor incididunt ut labore et Dolore magna aliqua ut enim .</p>
      </div>
      <div class="feature" style="left:175px">
        <div class="thumb" role="img" aria-label="Guard monitoring a wall of surveillance screens" style="background:linear-gradient(135deg,#3a4a5c,#8a9a88)"></div>
        <h4>Guard Services</h4>
        <p>Adipisicing elit eiusmod Tempor incididunt ut labore et Dolore magna aliqua ut enim .</p>
      </div>
      <div class="feature" style="left:350px">
        <div class="thumb" role="img" aria-label="Dome camera on a pole in front of city towers" style="background:linear-gradient(180deg,#5d9ad8,#b8cfe3)"></div>
        <h4>Fixed Camra Systems</h4>
        <p>Adipisicing elit eiusmod Tempor incididunt ut labore et Dolore magna aliqua ut enim .</p>
      </div>
    </section>
  </main>

  <footer class="footer">Copy right 2014 © Tavron. All rights reserved</footer>
</div>
</body>
</html>
```